Plakat-Design für Immobilienmakler und Baufinanzierer
Zielgruppe
Wir sind Immobilienmakler und Baufinanzierer und suchen ein hochwertiges Design, unsere Zielgruppe sind Kunden, die Ihr Haus verkaufen möchten. Für jeden erfolgreichen Verkauf spenden wir 5 % unserer Maklercourtage an einen Verein, den sich der Kunde aussuchen darf. Mit diesem Plakat wollen wir auf unsere Vereinsförderng aufmerksam machen und Vereine ansprechen.
Aufgabenstellung
Text: 'Wir spenden 5 % unserer Provision für Ihren Verein', 'Nur 1,99 % Maklercourtage', Logo, Kontaktdaten

```html
<!DOCTYPE html>
<html lang="de">
<head>
<meta charset="utf-8">
<title>Halvers Immobilien – Vereinsförderung</title>
<link rel="stylesheet" href="https://fonts.googleapis.com/css2?family=Playfair+Display:wght@400;800&family=Raleway:wght@400;600;700&display=swap">
<style>
  :root {
    --stage: #d8d8d4;
    --paper: #efeeea;
    --teal: #1f5e66;
    --stone: #8f8b86;
    --white: #ffffff;
  }
  * { margin: 0; padding: 0; box-sizing: border-box; }
  html, body { width: 1200px; height: 1200px; overflow: hidden; }
  body { background: var(--stage); position: relative; }

  .poster {
    position: absolute;
    left: 207px; top: 50px;
    width: 786px; height: 1100px;
    background: var(--paper);
    overflow: hidden;
    box-shadow: 0 6px 24px rgba(0,0,0,.18);
  }

  .brand {
    position: absolute;
    top: 100px; left: 0; width: 100%;
    display: flex; align-items: center; justify-content: center;
    gap: 14px;
  }
  .brand-mark {
    width: 26px; height: 26px;
    background: var(--teal);
  }
  .brand-name {
    font-family: "Raleway", sans-serif;
    font-weight: 600;
    font-size: 28px;
    letter-spacing: 2px;
    color: var(--teal);
  }

  .headline {
    position: absolute;
    top: 318px; left: 0; width: 100%;
    text-align: center;
    font-family: "Playfair Display", serif;
    color: var(--teal);
    font-size: 47px;
    line-height: 58px;
    text-transform: uppercase;
  }
  .headline .strong { font-weight: 800; }
  .headline .light { font-weight: 400; }

  .price-tag {
    position: absolute;
    left: 212px; top: 568px;
    width: 363px; height: 59px;
    background: var(--stone);
    color: var(--white);
    font-family: "Raleway", sans-serif;
    font-weight: 600;
    font-size: 21px;
    display: flex; align-items: center; justify-content: center;
  }

  .corner-mark {
    position: absolute;
    left: 632px; top: 853px;
    width: 72px; height: 72px;
    background: var(--teal);
  }

  .footer-band {
    position: absolute;
    left: 0; top: 937px;
    width: 100%; height: 163px;
    background: var(--teal);
  }
  .footer-rule {
    position: absolute;
    left: 38px; right: 0; top: 929px;
    height: 24px;
    background: var(--stone);
  }

  .contact {
    position: absolute;
    top: 1001px; left: 38px; right: 36px;
    display: flex; justify-content: space-between;
    font-family: "Raleway", sans-serif;
    font-size: 15px;
    line-height: 19px;
    color: var(--white);
  }
  .contact strong { font-weight: 700; }
  .contact-phone { padding-top: 19px; margin-left: 40px; }
  .contact-web { padding-top: 19px; text-align: right; }
</style>
</head>
<body>
  <main class="poster">
    <header class="brand">
      <div class="brand-mark"></div>
      <div class="brand-name">Halvers Immobilien</div>
    </header>

    <h1 class="headline">
      <span class="strong">Wir spenden 5&nbsp;%</span><br>
      <span class="light">unserer Provision</span><br>
      <span class="strong">für Ihren Verein</span>
    </h1>

    <div class="price-tag">Nur 1,99&nbsp;% Maklercourtage</div>

    <div class="corner-mark" role="img" aria-label="Platz für das Firmenzeichen"></div>

    <div class="footer-band"></div>
    <div class="footer-rule"></div>

    <footer class="contact">
      <div class="contact-address">
        <strong>Halvers Immobilien</strong><br>
        Amselweg 7<br>
        47800 Kornfeld
      </div>
      <div class="contact-phone">
        Tel: 02100 123 45 67<br>
        Mobil: 0150 000 123 45
      </div>
      <div class="contact-web">
        info@halvers-immobilien.de<br>
        www.halvers-immobilien.de
      </div>
    </footer>
  </main>
</body>
</html>
```